Business Card Design

Please see my website www.qvleading.com.au to for further information on my services and styling of my site
Updates

Project Deadline Extended
Reason: Deadline is extended to permit alterations to current designs or for any new submissions. Cheers

Industry/Entity Type

Business

Contact Information for Business Card

Marcus Belton
Empowerment Coach

'Live your passion'

marcus@qvleading.com.au
0437158206
qvleading.com.au

```html
<!DOCTYPE html>
<html lang="en">
<head>
<meta charset="utf-8">
<title>Quest Vitality Leading – Business Card</title>
<link rel="stylesheet" href="https://fonts.googleapis.com/css2?family=Oswald:wght@400;500&family=Open+Sans:wght@400&display=swap">
<style>
  :root {
    --ink: #111111;
    --lime: #b4ff00;
    --paper: #ffffff;
    --figure-light: #ffffff;
    --figure-dark: #8a8a8a;
  }
  html, body {
    margin: 0;
    padding: 0;
    width: 1200px;
    height: 742px;
    overflow: hidden;
    background: var(--paper);
  }
  .card {
    position: relative;
    width: 1200px;
    height: 742px;
    overflow: hidden;
    background: var(--ink);
  }
  .card__shapes {
    position: absolute;
    inset: 0;
    width: 1200px;
    height: 742px;
  }
  .band--lime { fill: var(--lime); }
  .tab--name { fill: var(--paper); }

  .brand-mark {
    position: absolute;
    left: 380px;
    top: 108px;
    width: 300px;
    text-align: center;
    margin: 0;
    font-family: "Oswald", sans-serif;
    font-weight: 500;
    font-size: 150px;
    line-height: 1;
    color: var(--lime);
    letter-spacing: 2px;
  }
  .brand-figures {
    position: absolute;
    left: 681px;
    top: 162px;
    width: 151px;
    height: 177px;
    background: linear-gradient(90deg, var(--figure-dark) 0%, var(--figure-dark) 30%, var(--figure-light) 45%, var(--figure-light) 100%);
    border-radius: 40px 40px 0 0;
    opacity: 0.9;
  }
  .business-name {
    position: absolute;
    left: 0;
    width: 1200px;
    top: 392px;
    margin: 0;
    text-align: center;
    font-family: "Oswald", sans-serif;
    font-weight: 400;
    font-size: 48px;
    line-height: 1.2;
    color: var(--ink);
    letter-spacing: 0.5px;
  }
  .service {
    position: absolute;
    top: 563px;
    margin: 0;
    font-family: "Open Sans", sans-serif;
    font-weight: 400;
    font-size: 30px;
    line-height: 1.2;
    color: var(--ink);
  }
  .service--strength { left: 104px; }
  .service--coaching { right: 119px; }
</style>
</head>
<body>
  <main class="card">
    <svg class="card__shapes" viewBox="0 0 555 343" preserveAspectRatio="none" aria-hidden="true">
      <rect class="band--lime" x="0" y="185" width="555" height="158"/>
      <path class="tab--name" d="M95,185 C115,185 120,157 142,157 L413,157 C435,157 440,185 460,185 C444,185 440,237 410,237 L145,237 C115,237 111,185 95,185 Z"/>
    </svg>

    <p class="brand-mark">QVL</p>
    <div class="brand-figures" role="img" aria-label="Silhouettes of two people raising their arms in celebration"></div>

    <h1 class="business-name">Quest Vitality Leading</h1>

    <p class="service service--strength">Strength &amp; Conditioning</p>
    <p class="service service--coaching">Empowerment Coaching</p>
  </main>
</body>
</html>
```